Web design for Crowdfunding site HopeWingsRally.com

We need a web design for christian crowdfunding website. Here is the challenge: We need responsive layout that is targeted first in iPad size of screen. It should also scale somehow down to iPhone size of screens. Web layout can be about the same size as iPad screen.

Screens should work so that main page scrolls not but only certain part of the screen scrolls and always one "page" at time. We can implement these "scrolls" then later with javascript but now we need only design. The challenge is to create this kind of hybrid website / app look.

Target is at first to raise funds to orphan people needing about $40 per month for their living and education. There is always some organization which takes care of these kids. Later there will be other christian missions included. At first we are looking to find monthly supporters.

You can be as creative as you want :) As you see from the look and feel sector, I am not looking any same traditional look which many "help kids" sites have. I am looking to reach now younger generation and therefore iPad and mobile are the main screen sizes.

Inspirational designs:
- https://example-gallery.test/profiles/studiofernlake/designs/482716?from=%2Fbrowse%2Fxhr%2Fdesigns%3Fcategory%3Dmobile-app-design
- http://www.artpoolhub.test/design/8261047 Clear, simple visuals
- http://www.artpoolhub.test/design/7394215 Header
- http://www.artpoolhub.test/design/6048392 Contrast in the colors, i think is powerfull

Some terms could be: Kids play, kids are learning (in the school). No static posture but living like kids are. I wonder also how we could also add little bit gaming style even though the question is of reali life of real people. Giving should be rewarding.

Target Market(s)

People who want help other people.

Industry/Entity Type

Christian

Number of Pages Required

4 page

Requirements
Must have
• Homepage. Mission page (In my wireframes it was one kid).
Nice to have
• Other pages and some idea how to scroll. 4 pages is no must. If you feel easy, please give first some draft and I give comments on that.

```html
<!DOCTYPE html>
<html lang="en">
<head>
<meta charset="utf-8">
<title>HopeWings Rally – Project Page Tablet View</title>
<link rel="stylesheet" href="https://fonts.googleapis.com/css2?family=Orbitron:wght@600;700;800&family=Open+Sans:wght@400;600;700&display=swap">
<style>
:root{
  --bg:#cfd5df;
  --bg-light:#dde2ea;
  --title:#5e5e63;
  --blue:#3a97d0;
  --blue-dark:#2b82b9;
  --hero-dark:#2a3f5a;
  --hero-warm:#7a5c52;
  --white:#ffffff;
  --page:#f4f4f4;
  --text:#3a3a3a;
  --muted:#9a9a9a;
  --line:#e3e3e3;
  --green:#1fbf7a;
  --yellow:#f0c419;
  --red:#e24b3b;
  --accent-gold:#f1b81f;
  --submit:#1fc27e;
}
*{box-sizing:border-box;margin:0;padding:0}
html,body{width:1200px;height:1089px;overflow:hidden}
body{
  background:linear-gradient(180deg,var(--bg-light),var(--bg));
  font-family:"Open Sans",Arial,sans-serif;color:var(--text);
  position:relative;
}
.showcase-title{
  position:absolute;top:58px;left:0;width:1200px;text-align:center;
  font-family:"Orbitron",sans-serif;font-weight:700;color:var(--title);
  font-size:37px;line-height:43px;letter-spacing:3px;
}
.screen{
  position:absolute;left:270px;width:660px;height:412px;overflow:hidden;
  background:var(--white);box-shadow:0 6px 18px rgba(40,50,70,.25);
}
.screen--projects{top:182px}
.screen--categories{top:642px;background:var(--page)}

/* hero */
.hero{position:absolute;left:0;top:0;width:660px;height:122px;
  background:linear-gradient(100deg,var(--hero-dark) 0%,#4a5468 45%,var(--hero-warm) 75%,#3b4a60 100%);
  text-align:center;color:var(--white)}
.hero__title{font-family:"Orbitron",sans-serif;font-weight:700;font-size:22px;letter-spacing:2px;margin-top:22px}
.hero__rule{width:50px;height:3px;background:var(--accent-gold);margin:9px auto 8px}
.hero__lead{font-size:11px;line-height:15px;font-weight:600}

/* breadcrumb bar */
.crumbs{position:absolute;left:0;top:122px;width:660px;height:32px;background:var(--blue);
  color:var(--white);font-size:9px;font-weight:700;display:flex;align-items:center}
.crumbs__path{display:flex;align-items:center;gap:6px;padding-left:14px;flex:1}
.crumbs__path svg{display:block}
.crumbs__tabs{display:flex;height:100%}
.crumbs__tab{display:flex;align-items:center;padding:0 13px;border-left:2px solid var(--white)}
.crumbs__tab:first-child{border-left:none}

/* project cards */
.card{position:absolute;background:var(--white);box-shadow:0 1px 4px rgba(0,0,0,.12);text-align:center}
.card__photo{width:100%;background:linear-gradient(180deg,#8fb36a,#5d8a3a)}
.card__photo--warm{background:linear-gradient(180deg,#c9a98a,#6f5a48)}
.card__photo--pale{background:linear-gradient(180deg,#dfe3e6,#a7b0b4)}
.card__name{font-family:"Orbitron",sans-serif;font-weight:700;font-size:8.5px;letter-spacing:.5px;margin-top:9px}
.card__rule{width:22px;height:2px;margin:4px auto 6px}
.rule--green{background:var(--green)}
.rule--yellow{background:var(--yellow)}
.rule--red{background:var(--red)}
.card__text{font-size:7.5px;line-height:10.5px;font-weight:600;padding:0 10px}
.card__stats{position:absolute;left:8px;right:6px;display:flex;align-items:center;justify-content:space-between}
.gauge{position:relative;width:54px;height:54px}
.gauge svg{display:block}
.gauge__value{position:absolute;left:0;top:16px;width:54px;text-align:center;font-size:10px;font-weight:600;color:#555}
.gauge__label{position:absolute;left:0;top:30px;width:54px;text-align:center;font-size:4.5px;color:var(--muted);letter-spacing:.3px}
.gauge__avatar{position:absolute;left:-4px;bottom:-6px;width:20px;height:20px;border-radius:50%;
  background:linear-gradient(180deg,#d8b795,#8a6d56);border:1.5px solid var(--white)}
.facts{text-align:left;font-size:5px;line-height:7px;color:var(--muted);width:40px}
.facts b{display:block;color:#444;font-size:5.5px}
.facts div{margin-bottom:4px}

/* sidebar */
.panel{position:absolute;background:var(--white);box-shadow:0 1px 4px rgba(0,0,0,.12)}
.panel__head{height:22px;background:var(--blue);color:var(--white);font-family:"Orbitron",sans-serif;
  font-weight:700;font-size:8px;padding:7px 9px 0;letter-spacing:.3px}
.panel__body{padding:8px 9px}
.field__label{font-size:7.5px;font-weight:700;margin:3px 0 3px}
.field__input{height:16px;border:1px solid var(--line);font-size:6.5px;color:var(--muted);
  padding:3px 5px;margin-bottom:4px;display:flex;justify-content:space-between;align-items:center}
.radio{display:flex;align-items:center;gap:6px;font-size:5.5px;color:#777;height:16px}
.radio i{width:8px;height:8px;border-radius:50%;border:1px solid #ccc;display:block;position:relative}
.radio i.on::after{content:"";position:absolute;left:1.5px;top:1.5px;width:3px;height:3px;border-radius:50%;background:var(--blue)}
.btn-submit{position:absolute;right:10px;bottom:18px;width:62px;height:15px;background:var(--submit);color:var(--white);
  font-family:"Orbitron",sans-serif;font-size:7px;font-weight:700;text-align:center;line-height:15px;border-radius:2px}

.cat-list{display:grid;grid-template-columns:1fr 1fr;row-gap:11px;padding:13px 12px 12px;font-size:6px;color:#777}
.cat-list span{display:flex;align-items:center;gap:5px}
.cat-list span::before{content:"";width:4px;height:4px;background:#666;border-radius:1px;display:block}
.share{display:flex;justify-content:center;gap:6px;padding:10px 0}
.share i{display:block;width:17px;height:17px;border-radius:50%}
.share .c1{background:#3b5d9b}.share .c2{background:#2b9be0}.share .c3{background:#e33b2e}.share .c4{background:#6d6d6d}
</style>
</head>
<body>

<h1 class="showcase-title">HOPEWINGS RALLY WEBSITE<br>PROJECT PAGE TABLET VIEW</h1>

<!-- Projects screen -->
<section class="screen screen--projects">
  <header class="hero" role="img" aria-label="Header photo of a child with a caregiver, dark blue and warm tones">
    <div class="hero__title">PROJECTS</div>
    <div class="hero__rule"></div>
    <p class="hero__lead">Pellentesque pharetra sapien non<br>quam placerat vestibulum.</p>
  </header>

  <nav class="crumbs">
    <div class="crumbs__path">
      <svg width="14" height="12" viewBox="0 0 14 12"><path d="M7 0 L14 6 H12 V12 H8.5 V8 H5.5 V12 H2 V6 H0 Z" fill="#fff"/></svg>
      <span>You Are Here: Home</span>
      <svg width="6" height="9" viewBox="0 0 6 9"><path d="M1 0 L6 4.5 L1 9 L0 8 L4 4.5 L0 1 Z" fill="#fff"/></svg>
      <span>Projects</span>
    </div>
    <div class="crumbs__tabs">
      <span class="crumbs__tab">Trending</span>
      <span class="crumbs__tab">Final Countdown</span>
      <span class="crumbs__tab">Most Funded</span>
    </div>
  </nav>

  <article class="card" style="left:35px;top:165px;width:120px;height:238px">
    <div class="card__photo" style="height:79px" role="img" aria-label="Photo of a laughing girl outdoors"></div>
    <div class="card__name">LOREM IPSUM</div><div class="card__rule rule--green"></div>
    <p class="card__text">Pellentesque pharetra sapien nonquam placerat vestibulum.</p>
    <div class="card__stats" style="top:160px">
      <div class="gauge">
        <svg width="54" height="54" viewBox="0 0 54 54"><circle cx="27" cy="27" r="22" fill="none" stroke="#eee" stroke-width="3"/><circle cx="27" cy="27" r="22" fill="none" stroke="var(--green)" stroke-width="3" stroke-dasharray="103.7 138.2" transform="rotate(-90 27 27)"/></svg>
        <div class="gauge__value">75%</div><div class="gauge__label">COMPLETED</div>
        <div class="gauge__avatar" role="img" aria-label="Small profile photo"></div>
      </div>
      <div class="facts"><div><b>12</b>DAYS LEFT</div><div><b>175</b>BACKERS</div><div><b>$57,000.00</b>FUNDED</div></div>
    </div>
  </article>

  <article class="card" style="left:169px;top:165px;width:120px;height:238px">
    <div class="card__photo" style="height:79px" role="img" aria-label="Photo of a smiling girl on grass"></div>
    <div class="card__name">LOREM IPSUM</div><div class="card__rule rule--yellow"></div>
    <p class="card__text">Pellentesque pharetra sapien nonquam placerat vestibulum.</p>
    <div class="card__stats" style="top:160px">
      <div class="gauge">
        <svg width="54" height="54" viewBox="0 0 54 54"><circle cx="27" cy="27" r="22" fill="none" stroke="#eee" stroke-width="3"/><circle cx="27" cy="27" r="22" fill="none" stroke="var(--yellow)" stroke-width="3" stroke-dasharray="117.5 138.2" transform="rotate(-90 27 27)"/></svg>
        <div class="gauge__value">85%</div><div class="gauge__label">COMPLETED</div>
        <div class="gauge__avatar" role="img" aria-label="Small profile photo"></div>
      </div>
      <div class="facts"><div><b>12</b>DAYS LEFT</div><div><b>175</b>BACKERS</div><div><b>$57,000.00</b>FUNDED</div></div>
    </div>
  </article>

  <article class="card" style="left:304px;top:165px;width:120px;height:238px">
    <div class="card__photo card__photo--warm" style="height:79px" role="img" aria-label="Photo of a smiling girl in a dark jacket"></div>
    <div class="card__name">LOREM IPSUM</div><div class="card__rule rule--red"></div>
    <p class="card__text">Pellentesque pharetra sapien nonquam placerat vestibulum.</p>
    <div class="card__stats" style="top:160px">
      <div class="gauge">
        <svg width="54" height="54" viewBox="0 0 54 54"><circle cx="27" cy="27" r="22" fill="none" stroke="#eee" stroke-width="3"/><circle cx="27" cy="27" r="22" fill="none" stroke="var(--blue-dark)" stroke-width="3" stroke-dasharray="89.8 138.2" transform="rotate(-90 27 27)"/></svg>
        <div class="gauge__value">65%</div><div class="gauge__label">COMPLETED</div>
        <div class="gauge__avatar" role="img" aria-label="Small profile photo"></div>
      </div>
      <div class="facts"><div><b>12</b>DAYS LEFT</div><div><b>175</b>BACKERS</div><div><b>$57,000.00</b>FUNDED</div></div>
    </div>
  </article>

  <aside class="panel" style="left:447px;top:165px;width:176px;height:235px">
    <div class="panel__head">Search Projects</div>
    <div class="panel__body">
      <div class="field__label">Categories</div><div class="field__input">All Categories</div>
      <div class="field__label">City</div><div class="field__input">City name</div>
      <div class="field__label">Country</div>
      <div class="field__input">All Countries<svg width="7" height="5" viewBox="0 0 7 5"><path d="M0 0 L3.5 4 L7 0" fill="none" stroke="#999" stroke-width="1"/></svg></div>
      <div class="field__label">Percent Funded</div>
      <div class="radio"><i class="on"></i>All</div>
      <div class="radio"><i></i>50% - 75%</div>
      <div class="radio"><i></i>75% - 100%</div>
    </div>
    <div class="btn-submit">SUBMIT</div>
  </aside>
</section>

<!-- Categories screen -->
<section class="screen screen--categories">
  <article class="card" style="left:18px;top:79px;width:132px;height:262px">
    <div class="card__photo card__photo--warm" style="height:86px" role="img" aria-label="Photo of a smiling girl with curly hair"></div>
    <div class="card__name">LOREM IPSUM</div><div class="card__rule rule--green"></div>
    <p class="card__text">Pellentesque pharetra sapien nonquam placerat vestibulum.</p>
    <div class="card__stats" style="top:174px">
      <div class="gauge">
        <svg width="54" height="54" viewBox="0 0 54 54"><circle cx="27" cy="27" r="22" fill="none" stroke="#eee" stroke-width="3"/><circle cx="27" cy="27" r="22" fill="none" stroke="var(--green)" stroke-width="3" stroke-dasharray="103.7 138.2" transform="rotate(-90 27 27)"/></svg>
        <div class="gauge__value">75%</div><div class="gauge__label">COMPLETED</div>
        <div class="gauge__avatar" role="img" aria-label="Small profile photo"></div>
      </div>
      <div class="facts"><div><b>12</b>DAYS LEFT</div><div><b>175</b>BACKERS</div><div><b>$57,000.00</b>FUNDED</div></div>
    </div>
  </article>

  <article class="card" style="left:165px;top:79px;width:132px;height:262px">
    <div class="card__photo" style="height:86px" role="img" aria-label="Photo of a blonde toddler resting on grass"></div>
    <div class="card__name">LOREM IPSUM</div><div class="card__rule rule--yellow"></div>
    <p class="card__text">Pellentesque pharetra sapien nonquam placerat vestibulum.</p>
    <div class="card__stats" style="top:174px">
      <div class="gauge">
        <svg width="54" height="54" viewBox="0 0 54 54"><circle cx="27" cy="27" r="22" fill="none" stroke="#eee" stroke-width="3"/><circle cx="27" cy="27" r="22" fill="none" stroke="var(--yellow)" stroke-width="3" stroke-dasharray="117.5 138.2" transform="rotate(-90 27 27)"/></svg>
        <div class="gauge__value">85%</div><div class="gauge__label">COMPLETED</div>
        <div class="gauge__avatar" role="img" aria-label="Small profile photo"></div>
      </div>
      <div class="facts"><div><b>12</b>DAYS LEFT</div><div><b>175</b>BACKERS</div><div><b>$57,000.00</b>FUNDED</div></div>
    </div>
  </article>

  <article class="card" style="left:313px;top:79px;width:132px;height:262px">
    <div class="card__photo card__photo--pale" style="height:86px" role="img" aria-label="Photo of a girl with a hair bow in a bright room"></div>
    <div class="card__name">LOREM IPSUM</div><div class="card__rule rule--red"></div>
    <p class="card__text">Pellentesque pharetra sapien nonquam placerat vestibulum.</p>
    <div class="card__stats" style="top:174px">
      <div class="gauge">
        <svg width="54" height="54" viewBox="0 0 54 54"><circle cx="27" cy="27" r="22" fill="none" stroke="#eee" stroke-width="3"/><circle cx="27" cy="27" r="22" fill="none" stroke="var(--blue-dark)" stroke-width="3" stroke-dasharray="89.8 138.2" transform="rotate(-90 27 27)"/></svg>
        <div class="gauge__value">65%</div><div class="gauge__label">COMPLETED</div>
        <div class="gauge__avatar" role="img" aria-label="Small profile photo"></div>
      </div>
      <div class="facts"><div><b>12</b>DAYS LEFT</div><div><b>175</b>BACKERS</div><div><b>$57,000.00</b>FUNDED</div></div>
    </div>
  </article>

  <aside class="panel" style="left:461px;top:79px;width:174px;height:262px">
    <div class="panel__head">Popular Categories</div>
    <div class="cat-list">
      <span>Animals</span><span>Art</span>
      <span>Community</span><span>Dance</span>
      <span>Design</span><span>Education</span>
      <span>Environment</span><span>Fashion</span>
      <span>Film</span><span>Food</span>
      <span>Gaming</span><span>Health</span>
      <span>Music</span><span>Politics</span>
    </div>
    <div class="panel__head" style="height:18px;padding-top:5px">Find This Project On</div>
    <div class="share"><i class="c1"></i><i class="c2"></i><i class="c3"></i><i class="c4"></i></div>
  </aside>
</section>

</body>
</html>
```